Security Consulting firm needs an ad design

We need a 3.375” x 4.875” ad design for our core services. The ad should include the company logo and the content from the first half of the attached sample JPG (Without the sentence under the title but including the description for the Plan - Design - Deploy - Manage and the titles ) as well as the following corporate information:
www.harrowfieldco.us
82 Marrow Ave. Suite 615, Pinecrest Hollow, NJ 07381
PHONE 888-412-6057 / EMAIL info@harrowfieldco.us
The design should incorporate the same blue color that is in our logo and the font Raleway. Also - please use the same icons that are in the sample JPG - they can also be extracted from the attached indesign file.
The ad is to be publish in print and digital issue.
Please provide with all source files as well as a hi-res PDF using press quality or similar PDF settings.
- Raleway

```html
<!DOCTYPE html>
<html lang="en">
<head>
<meta charset="utf-8">
<title>Harrowfield Consulting – Creating Secure Environment</title>
<link rel="stylesheet" href="https://fonts.googleapis.com/css2?family=Raleway:ital,wght@0,300;0,400;0,500;0,600;0,700;0,800;1,300&display=swap">
<style>
  :root {
    --brand-blue: #2473c1;
    --brand-blue-soft: #5b8fd6;
    --brand-blue-deep: #0f5fae;
    --panel-grey: #f2f2f3;
    --band-grey: #e6e7e9;
    --ink: #1d1d22;
    --white: #ffffff;
    --gold-light: #f4dca6;
    --gold-mid: #d9a866;
    --gold-dark: #9a7350;
  }
  * { box-sizing: border-box; margin: 0; padding: 0; }
  html, body { width: 831px; height: 1200px; overflow: hidden; background: var(--white); }
  body { font-family: "Raleway", sans-serif; color: var(--ink); }
  .ad { position: relative; width: 831px; height: 1200px; overflow: hidden; background: var(--white); }
  .ad-shapes { position: absolute; inset: 0; }

  .headline { position: absolute; left: 58px; top: 272px; color: var(--white); line-height: 1; }
  .headline__lead { display: block; font-weight: 400; font-size: 52px; letter-spacing: 0.5px; }
  .headline__key { display: block; font-weight: 800; font-size: 108px; margin-top: -6px; letter-spacing: -1.5px; }
  .headline__tail { display: block; font-weight: 800; font-size: 80px; margin-top: -2px; letter-spacing: -0.5px; }

  .brand { position: absolute; left: 612px; top: 352px; display: flex; align-items: center; gap: 6px; }
  .brand__dot { width: 14px; height: 14px; border-radius: 50%; background: var(--brand-blue); flex: none; }
  .brand__name { font-weight: 700; font-size: 16px; color: var(--brand-blue); line-height: 1; white-space: nowrap; }

  .services-tab {
    position: absolute; left: 70px; top: 618px; width: 334px; height: 30px;
    background: linear-gradient(90deg, var(--brand-blue) 0%, var(--brand-blue-soft) 70%, #c9d7ee 100%);
    border-radius: 4px;
  }
  .services-tab__label { position: absolute; left: 16px; top: -1px; font-style: italic; font-weight: 300; font-size: 29px; color: var(--white); line-height: 32px; }

  .service { position: absolute; }
  .service__title { font-weight: 500; font-size: 33px; line-height: 1; color: var(--ink); }
  .service__text { font-weight: 500; font-size: 17px; line-height: 25px; color: var(--ink); margin-top: 4px; }
  .service--plan { left: 160px; top: 685px; }
  .service--deploy { left: 508px; top: 685px; }
  .service--design { left: 166px; top: 788px; }
  .service--manage { left: 508px; top: 788px; }

  .contact { position: absolute; left: 94px; top: 940px; font-weight: 600; font-size: 15.5px; line-height: 23px; color: var(--ink); font-style: normal; }

  .website { position: absolute; left: 551px; top: 1100px; font-weight: 500; font-size: 20px; color: var(--white); }
</style>
</head>
<body>
<main class="ad">
  <svg class="ad-shapes" width="831" height="1200" viewBox="0 0 831 1200">
    <defs>
      <linearGradient id="cityGlow" x1="0" y1="0" x2="1" y2="1">
        <stop offset="0" stop-color="#e9e2d6"/>
        <stop offset="0.35" stop-color="#f4dca6"/>
        <stop offset="0.65" stop-color="#d9a866"/>
        <stop offset="1" stop-color="#9a7350"/>
      </linearGradient>
      <linearGradient id="waveBack" x1="0" y1="0" x2="1" y2="0">
        <stop offset="0" stop-color="#e7eef8"/>
        <stop offset="1" stop-color="#4f86cf"/>
      </linearGradient>
      <linearGradient id="waveFront" x1="0" y1="0" x2="1" y2="0">
        <stop offset="0" stop-color="#0f5fae"/>
        <stop offset="0.5" stop-color="#3d86d2"/>
        <stop offset="1" stop-color="#2473c1"/>
      </linearGradient>
    </defs>

    <rect class="hero-photo" x="0" y="0" width="831" height="558" fill="url(#cityGlow)" role="img" aria-label="Photo of a sunlit city skyline overlaid with glowing chain links, a padlock and wireframe cubes"/>

    <polygon class="hero-panel" points="0,200 361,200 566,558 0,558" fill="var(--brand-blue-soft)" opacity="0.92"/>

    <rect class="brand-band" x="435" y="324" width="396" height="283" fill="var(--band-grey)"/>
    <rect x="0" y="558" width="440" height="49" fill="var(--white)"/>
    <polygon class="brand-stripe" points="435,324 497,324 656,607 590,607" fill="var(--brand-blue)"/>
    <polygon class="brand-stripe-gap" points="497,324 541,324 700,607 656,607" fill="var(--white)"/>
    <polygon class="brand-stripe" points="541,324 595,324 755,607 700,607" fill="var(--brand-blue)"/>

    <rect class="card-shadow" x="55" y="668" width="732" height="238" rx="26" fill="var(--brand-blue)"/>
    <rect class="card" x="69" y="658" width="732" height="238" rx="26" fill="var(--panel-grey)"/>

    <g class="icon icon--plan" transform="translate(115 710)">
      <circle r="29" fill="var(--white)"/>
      <rect x="-11" y="-14" width="22" height="29" rx="2" fill="none" stroke="var(--brand-blue)" stroke-width="2.5"/>
      <rect x="-5" y="-18" width="10" height="6" rx="1.5" fill="var(--brand-blue)"/>
      <path d="M-7 -6 l2 2 l3 -4 M-7 1 l2 2 l3 -4 M-7 8 l2 2 l3 -4" fill="none" stroke="var(--brand-blue)" stroke-width="1.8"/>
      <path d="M1 -5 h6 M1 2 h6 M1 9 h6" stroke="var(--brand-blue)" stroke-width="1.8"/>
    </g>
    <g class="icon icon--deploy" transform="translate(453 714)">
      <circle r="29" fill="var(--white)"/>
      <g transform="rotate(45)">
        <path d="M0 -18 C8 -10 8 4 5 10 H-5 C-8 4 -8 -10 0 -18 Z" fill="var(--brand-blue)"/>
        <circle cy="-5" r="3" fill="var(--white)"/>
        <path d="M-5 2 L-11 10 L-5 9 Z M5 2 L11 10 L5 9 Z" fill="var(--brand-blue)"/>
        <path d="M-3 12 L0 19 L3 12 Z" fill="var(--brand-blue-soft)"/>
      </g>
    </g>
    <g class="icon icon--design" transform="translate(116 813)">
      <circle r="29" fill="var(--white)"/>
      <circle r="11" fill="none" stroke="var(--brand-blue)" stroke-width="7" stroke-dasharray="4.3 2.6"/>
      <circle r="8" fill="none" stroke="var(--brand-blue)" stroke-width="3"/>
      <path d="M0 0 L14 14" stroke="var(--brand-blue)" stroke-width="5" stroke-linecap="round"/>
    </g>
    <g class="icon icon--manage" transform="translate(453 812)">
      <circle r="29" fill="var(--white)"/>
      <circle cy="-10" r="5" fill="var(--brand-blue)"/>
      <path d="M-8 5 C-8 -4 8 -4 8 5 Z" fill="var(--brand-blue)"/>
      <path d="M-15 6 H15 M0 6 V15" stroke="var(--brand-blue)" stroke-width="2"/>
      <circle cx="-16" cy="6" r="3" fill="var(--brand-blue)"/>
      <circle cx="16" cy="6" r="3" fill="var(--brand-blue)"/>
      <circle cy="16" r="3" fill="var(--brand-blue)"/>
    </g>

    <rect class="contact-rail" x="63" y="938" width="20" height="76" rx="5" fill="var(--brand-blue)"/>
    <g fill="none" stroke="var(--white)" stroke-width="1.5">
      <circle cx="73" cy="952" r="7"/>
      <path d="M73 948.5 a2.5 2.5 0 1 1 0.01 0 M73 954 v2.5"/>
      <circle cx="73" cy="976" r="7"/>
      <path d="M70 973 q0 6 6 6"/>
      <circle cx="73" cy="999" r="7"/>
      <path d="M69.5 1000 l7 -4 l-2.5 7 l-1 -2.5 z"/>
    </g>

    <path class="wave-back" d="M0 1200 V1090 C120 1040 250 1080 360 1110 C470 1140 560 1040 660 980 C740 935 800 940 831 945 V1200 Z" fill="url(#waveBack)" opacity="0.85"/>
    <path class="wave-front" d="M0 1200 V1118 C70 1075 170 1080 260 1110 C340 1136 420 1128 500 1060 C580 995 690 950 790 955 L831 958 V1200 Z" fill="url(#waveFront)"/>
    <path class="wave-base" d="M0 1200 V1170 C200 1150 500 1185 831 1160 V1200 Z" fill="var(--brand-blue-deep)" opacity="0.7"/>
  </svg>

  <h1 class="headline">
    <span class="headline__lead">Creating</span>
    <span class="headline__key">Secure</span>
    <span class="headline__tail">Enviroment</span>
  </h1>

  <div class="brand">
    <span class="brand__dot"></span>
    <span class="brand__name">Harrowfield Consulting</span>
  </div>

  <div class="services-tab"><span class="services-tab__label">Our services includes</span></div>

  <section class="service service--plan">
    <h2 class="service__title">Plan</h2>
    <p class="service__text">Security assessment and<br>planning services</p>
  </section>
  <section class="service service--deploy">
    <h2 class="service__title">Deploy</h2>
    <p class="service__text">Procurement and project<br>management services</p>
  </section>
  <section class="service service--design">
    <h2 class="service__title">Design</h2>
    <p class="service__text">Security design and<br>engineering</p>
  </section>
  <section class="service service--manage">
    <h2 class="service__title">Manage</h2>
    <p class="service__text">Comprehesive securiy<br>management</p>
  </section>

  <address class="contact">
    82 Marrow Ave. Suite 615, Pinecrest Hollow, NJ 07381<br>
    PHONE 888-412-6057 /<br>
    EMAIL info@harrowfieldco.us
  </address>

  <div class="website">www.harrowfieldco.us</div>
</main>
</body>
</html>
```